Velmo Swinger site - new website, blogsite and merchandise point, connection to tradeva

We are a well established Swingers Club in the North east of UK and already have an existing site. www.velmo-example.co.uk, BUT we have changed our logo and our information on the site needs to be updated.

We are changing our hosting site to Nimbrashost.example ,also wanting to start a blog which is linked to the club, plus we wish to sell a small exclusive range of Velmo linked merchandise which will also be available on Tradeva.

I have attached a pdf of the majority of the content. additionally we will provide pictures and a videoclip which should be able to be viewed by pc's, lap tops and mobile phones (the whole website must be fully accessible via phone).

The new site must be able to be updated by someone with medium computer knowledge (usually me), by no means expert. Updates will generally be new pictures and written information. The site must be able to be transferred to NimbrasHost.

Velmo is one of the countries leading clubs and emphasises friendliness, fun & safety for its members, we look after you to ensure your experience is the best we can offer. We are very proud of our reputation, built up over more than 10 years.

Target Market(s)

Swingers, dreamers & fantasists, alternative lifestyle people

Coding

Coded - Design and coding required

Number of Pages Required

5+ page

Font styles to use
Sans Serif

Colors
000000
ec1f27
fbfbfb
eeeeee
eaeaea

Requirements
Must have
• website with blog attached, link to tradeva & quidlo, ability to run videoclip and picture album and must be compatable to transfer easily to Nimbrashost and be updated by non-professional (who can learn)
• Straightforward & easy to navigate
• over 18 content page with enter button
Nice to have
• sexy site
• link to chirpster maybe
• black site would be nice with red or white writing
Should not have
• children and animals in anyway shape or form

```html
<!DOCTYPE html>
<html lang="en">
<head>
<meta charset="utf-8">
<title>Velmo – A true Swingers Club</title>
<link rel="stylesheet" href="https://fonts.googleapis.com/css2?family=Bree+Serif&family=Poppins:wght@400;500;600&display=swap">
<style>
:root{
  --black:#000000;
  --red:#ec1f27;
  --white:#fbfbfb;
  --light:#eeeeee;
  --grey:#eaeaea;
  --header:#1d1311;
  --card:#141414;
  --amber:#f4b72f;
}
*{margin:0;padding:0;box-sizing:border-box}
html,body{width:1200px;height:2466px;overflow:hidden;background:var(--black)}
body{position:relative;font-family:'Poppins',sans-serif;color:var(--white)}
.abs{position:absolute}

.site-header{left:0;top:0;width:1200px;height:79px;background:var(--header);display:flex;align-items:center;justify-content:center}
.brand{font-family:'Bree Serif',serif;font-size:46px;color:var(--white);letter-spacing:2px;line-height:1}
.main-nav{left:0;top:79px;width:1200px;height:36px;background:var(--red);display:flex;align-items:center;padding-left:98px}
.main-nav a{color:var(--white);text-decoration:none;font-size:12.5px;font-weight:500;white-space:nowrap}

.hero{left:0;top:115px;width:1200px;height:464px;background:linear-gradient(90deg,#3a2c22 0%,#5e4634 35%,#6e5a48 60%,#8a7c6c 85%,#7a6a58 100%)}
.hero-shade{left:0;top:115px;width:1200px;height:464px;background:rgba(0,0,0,.28)}
.hero-title{left:0;top:262px;width:1200px;text-align:center;font-family:'Bree Serif',serif;font-weight:400;font-size:36px;line-height:64px;color:var(--white)}
.btn-call{left:480px;top:408px;width:247px;height:44px;background:var(--red);color:var(--white);font-family:'Bree Serif',serif;font-size:24px;display:flex;align-items:center;justify-content:center}
.dots{display:flex;gap:3px}
.dot{width:10px;height:10px;border-radius:50%;border:2px solid var(--white);position:relative}
.dot::after{content:"";position:absolute;left:2px;top:2px;width:2px;height:2px;border-radius:50%;background:var(--white)}

.section-title{left:0;width:1200px;text-align:center;font-family:'Bree Serif',serif;font-weight:400;font-size:25px;color:var(--white)}
.section-text{text-align:center;font-size:10.5px;line-height:21.5px;color:var(--white)}
.section-text b{font-weight:600}

.feature{top:773px;width:273px;height:218px;background:var(--card);text-align:center}
.feature-head{display:flex;align-items:center;justify-content:center;gap:14px;margin-top:32px;height:44px}
.feature-head h3{font-family:'Bree Serif',serif;font-weight:400;font-size:22px}
.feature p{font-size:10.5px;line-height:20.5px;padding:0 28px;margin-top:32px}

.promo-photo{left:0;top:1098px;width:605px;height:258px;background:linear-gradient(160deg,#8a7250 0%,#c9b48f 30%,#e9ecea 55%,#d7dcd8 75%,#9c7e55 100%)}
.promo-panel{left:605px;top:1098px;width:595px;height:258px;background:linear-gradient(115deg,#1e1e1e 0%,#2a2a2a 60%,#111 61%,#222 100%)}
.promo-brand{left:605px;top:1118px;width:550px;text-align:center;font-size:22px;font-weight:500;color:var(--white)}
.promo-brand .sep{display:inline-block;width:1px;height:30px;background:var(--white);vertical-align:middle;margin:0 16px}
.promo-title{left:605px;top:1185px;width:550px;text-align:center;font-size:21px;color:var(--white)}
.promo-offer{left:605px;top:1228px;width:550px;text-align:center;font-size:15px;line-height:24px;font-weight:600;color:var(--red)}
.promo-rule{top:1252px;height:1px;background:var(--white);width:95px}
.btn-buy{left:763px;top:1289px;width:178px;height:46px;background:var(--amber);border-radius:3px;color:#111;display:flex;align-items:center;justify-content:center;gap:6px;font-size:15px;font-weight:500}
.btn-buy strong{font-size:19px;font-weight:600}

.post{top:1529px;width:310px;height:416px;background:var(--card)}
.post-photo{width:310px;height:230px}
.post p{font-size:10.5px;line-height:20.5px;text-align:center;padding:22px 22px 0}

.plan{top:2126px;width:281px;height:251px;border-radius:4px}
.plan-price{display:flex;flex-direction:column;align-items:center;justify-content:center;color:var(--white)}
.plan-price .amount{font-size:30px;font-weight:600;line-height:1}
.plan-price .amount small{font-size:15px;font-weight:500}
.plan-price .who{font-size:19px;margin-top:6px}

.site-footer{left:0;top:2408px;width:1200px;height:58px;background:var(--red);display:flex;align-items:center;justify-content:center;font-size:12.5px;font-weight:500}
</style>
</head>
<body>

<header class="abs site-header"><span class="brand">VELMO</span></header>

<nav class="abs main-nav">
  <a>Home</a>
  <a style="margin-left:55px">Diary</a>
  <a style="margin-left:60px">Theme Parties</a>
  <a style="margin-left:62px">TV/TG and Admirers</a>
  <a style="margin-left:59px">Membership</a>
  <a style="margin-left:58px">FAQs</a>
  <a style="margin-left:60px">Rooms</a>
  <a style="margin-left:58px">Contact US</a>
  <a style="margin-left:58px">Links</a>
</nav>

<div class="abs hero" role="img" aria-label="Hotel-style bedroom with a low bed, desk and latticed wall panel"></div>
<div class="abs hero-shade"></div>
<h1 class="abs hero-title">A true Swingers Club Where You Can Meet,<br>Socialise And Play (if you want.......)</h1>
<div class="abs btn-call">Call Us Today</div>
<div class="abs dots" style="left:584px;top:544px"><span class="dot"></span><span class="dot"></span><span class="dot"></span></div>

<h2 class="abs section-title" style="top:624px">A Great Place To Meet And Play!</h2>
<p class="abs section-text" style="left:160px;top:672px;width:880px">Velmo was established in Harlow Bridge in 2006 by Tomas (now retired) and has been at this location in Westmere and run by Mara since 2011. During this time we have upgraded and improved the club beyond recognition. We have a varied group of all sorts of people that work here and help here and because of this we can understand most fetishes and sexual orientations, all the people that help and work here do so because they love this environment <b>Read More</b></p>

<article class="abs feature" style="left:166px">
  <div class="feature-head">
    <svg width="34" height="38" viewBox="0 0 34 38" aria-hidden="true"><g fill="var(--red)"><rect x="2" y="2" width="4" height="20"/><rect x="2" y="2" width="14" height="4"/><rect x="12" y="6" width="4" height="4"/><rect x="0" y="20" width="34" height="4"/><path d="M2 24h30l-3 10H5z"/><rect x="6" y="34" width="4" height="4"/><rect x="24" y="34" width="4" height="4"/></g></svg>
    <h3>Hot Tub</h3>
  </div>
  <p>Lorem Ipsum is simply dummy text of the printing and typesetting industry. Lorem Ipsum has been the industry's standard dummy text ever since the 1500s</p>
</article>
<article class="abs feature" style="left:462px">
  <div class="feature-head">
    <svg width="30" height="36" viewBox="0 0 30 36" aria-hidden="true"><path fill="var(--red)" fill-rule="evenodd" d="M0 0h30v36H0zM4 4v12h9V4zm13 0v12h9V4zM4 20v12h9V20zm13 0v12h9V20z"/></svg>
    <h3>Steam Room</h3>
  </div>
  <p>Lorem Ipsum is simply dummy text of the printing and typesetting industry. Lorem Ipsum has been the industry's standard dummy text ever since the 1500s</p>
</article>
<article class="abs feature" style="left:758px">
  <div class="feature-head">
    <svg width="52" height="34" viewBox="0 0 52 34" aria-hidden="true"><g fill="var(--red)"><rect x="4" y="0" width="44" height="10"/><rect x="0" y="12" width="52" height="16"/><rect x="2" y="28" width="5" height="6"/><rect x="45" y="28" width="5" height="6"/></g></svg>
    <h3>Dark Room</h3>
  </div>
  <p>Lorem Ipsum is simply dummy text of the printing and typesetting industry. Lorem Ipsum has been the industry's standard dummy text ever since the 1500s</p>
</article>
<div class="abs dots" style="left:1075px;top:861px;flex-direction:column"><span class="dot"></span><span class="dot"></span><span class="dot"></span></div>

<div class="abs promo-photo" role="img" aria-label="White jacuzzi hot tub set in a wooden deck"></div>
<div class="abs promo-panel"></div>
<div class="abs promo-brand">Tradeva exclusive<span class="sep"></span>VELMO</div>
<div class="abs promo-title">Get Our Membership</div>
<div class="abs promo-offer">Never Before<br>Grab The Offer Now</div>
<div class="abs promo-rule" style="left:677px"></div>
<div class="abs promo-rule" style="left:927px"></div>
<div class="abs btn-buy">Buy From <strong>tradeva</strong></div>

<h2 class="abs section-title" style="top:1402px">From Our Blog</h2>
<p class="abs section-text" style="left:140px;top:1453px;width:920px">Lorem Ipsum is simply dummy text of the printing and typesetting industry. Lorem Ipsum has been the industry's standard dummy text ever since the 1500sLorem Ipsum is simply dummy text of the printing and typesetting industry. Lorem Ipsum has been the industry's standard dummy text ever since the 1500s</p>

<article class="abs post" style="left:94px">
  <div class="post-photo" role="img" aria-label="Attic bedroom with patterned wallpaper and skylight" style="background:linear-gradient(135deg,#6b4e48,#b7a39a 45%,#e7e2dc 70%,#7a2a2a)"></div>
  <p>Lorem Ipsum is simply dummy text of the printing and typesetting industry. Lorem Ipsum has been the industry's standard dummy text ever since the 1500sLorem Ipsum is simply dummy text of the printing and typesetting industry. Lorem Ipsum has been the industry's standard dummy text ever since the 1500s</p>
</article>
<article class="abs post" style="left:441px">
  <div class="post-photo" role="img" aria-label="Red-walled bedroom with two beds and warm lamps" style="background:linear-gradient(135deg,#6a1f18,#b8412e 45%,#8a2a22 70%,#3d0f0c)"></div>
  <p>Lorem Ipsum is simply dummy text of the printing and typesetting industry. Lorem Ipsum has been the industry's standard dummy text ever since the 1500sLorem Ipsum is simply dummy text of the printing and typesetting industry. Lorem Ipsum has been the industry's standard dummy text ever since the 1500s</p>
</article>
<article class="abs post" style="left:786px">
  <div class="post-photo" role="img" aria-label="Hotel bedroom with white bedding and a city print on the wall" style="background:linear-gradient(135deg,#4a4036,#a2937f 40%,#e8e2d6 65%,#5b4b3a)"></div>
  <p>Lorem Ipsum is simply dummy text of the printing and typesetting industry. Lorem Ipsum has been the industry's standard dummy text ever since the 1500sLorem Ipsum is simply dummy text of the printing and typesetting industry. Lorem Ipsum has been the industry's standard dummy text ever since the 1500s</p>
</article>

<h2 class="abs section-title" style="top:1977px">Velmo Membership</h2>
<p class="abs section-text" style="left:130px;top:2026px;width:940px">Sometimes we put new memberships on hold for certain categories, this is a private member's club and if we restrict membership it's for good reason, mainly to keep the balance right. If you already know a member then ask them to introduce you, (ask them to call or write so your name is on the guest list) or phone on the Velmo phone to arrange your first visit. The club phone is switched on from 2pm on the days we open (Thu/Fri/Sun).</p>

<div class="abs plan" style="left:150px;background:linear-gradient(160deg,#c9d3d8,#c79a7e 45%,#a4463c 80%,#6c6f86)" role="img" aria-label="Couple, membership for couples"></div>
<div class="abs plan plan-price" style="left:459px;background:linear-gradient(160deg,#e2483f,#d92f2a 60%,#b8221f)" role="img" aria-label="Young man, membership for single guys">
  <span class="amount">£30.00 <small>per</small></span>
  <span class="who">Single Guy</span>
</div>
<div class="abs plan" style="left:768px;background:linear-gradient(160deg,#8fb4b6,#3f7f86 45%,#c7a08a 75%,#6d5549)" role="img" aria-label="Young woman, membership for single ladies"></div>

<footer class="abs site-footer">copyright © 2017 Velmo. All Rights Reserved. Privacy Policy.</footer>

</body>
</html>
```